Redesign of business card for Cedar Ridge Mechanical

We are looking for a new design for our business cards for Cedar Ridge Mechanical. We are a plumbing & HVAC construction company, operating on the West Coast of Canada and USA. Logo attached.
Industry/Entity Type
Construction - Plumbing & HVAC
Contact Information for Business Card
Name, address, phone numbers, email, website address
Look and feel
Each slider illustrates characteristics of the customer's brand and the style your logo design should communicate.

```html
<!DOCTYPE html>
<html lang="en">
<head>
<meta charset="utf-8">
<title>Cedar Ridge Mechanical – Business Card</title>
<link rel="stylesheet" href="https://fonts.googleapis.com/css2?family=Montserrat:wght@400;500;600;700&display=swap">
<style>
  :root {
    --backdrop: #9b9b9b;
    --card-light: #ffffff;
    --card-dark: #252525;
    --ink: #1e1e1e;
    --ink-inverse: #ffffff;
  }
  * { margin: 0; padding: 0; box-sizing: border-box; }
  html, body {
    width: 1093px; height: 1200px; overflow: hidden;
    background: var(--backdrop);
    font-family: "Montserrat", Arial, sans-serif;
    color: var(--ink);
  }
  .canvas { position: relative; width: 1093px; height: 1200px; }
  .card {
    position: absolute; left: 265px; width: 596px; height: 364px;
    border-radius: 18px;
  }
  .card--front { top: 225px; background: var(--card-light); }
  .card--back  { top: 616px; background: var(--card-dark); }

  .brand {
    position: absolute; display: flex; align-items: center;
    font-weight: 700; text-transform: uppercase; line-height: 1.1;
  }
  .brand__mark { flex: none; border-radius: 3px; }
  .card--front .brand { left: 88px; top: 158px; width: 170px; gap: 10px; font-size: 15px; color: var(--ink); }
  .card--front .brand__mark { width: 26px; height: 26px; background: var(--ink); }
  .card--back .brand {
    left: 0; right: 0; top: 128px; justify-content: center; gap: 18px;
    font-size: 30px; color: var(--ink-inverse);
  }
  .card--back .brand__mark { width: 52px; height: 52px; background: var(--ink-inverse); border-radius: 5px; }

  .divider {
    position: absolute; left: 280px; top: 120px; width: 1.5px; height: 167px;
    background: var(--ink);
  }
  .contact { position: absolute; left: 295px; top: 120px; }
  .contact__name { font-size: 21px; font-weight: 700; letter-spacing: 0.3px; line-height: 1; }
  .contact__title { font-size: 12.5px; font-weight: 500; margin-top: 6px; }
  .contact__address { font-size: 13.5px; line-height: 16px; margin-top: 17px; }
  .contact__list { list-style: none; margin-top: 10px; }
  .contact__item {
    display: flex; align-items: center; gap: 9px;
    font-size: 13.5px; height: 16px; margin-top: 9px;
  }
  .contact__item svg { width: 13px; height: 13px; flex: none; fill: var(--ink); }
</style>
</head>
<body>
<main class="canvas">
  <section class="card card--front">
    <div class="brand">
      <span class="brand__mark"></span>
      <span class="brand__name">Cedar Ridge Mechanical</span>
    </div>
    <div class="divider"></div>
    <div class="contact">
      <p class="contact__name">Daniel Carter</p>
      <p class="contact__title">Managing Director</p>
      <p class="contact__address">240 Birch Hollow Lane<br>Fairview, MS 39170</p>
      <ul class="contact__list">
        <li class="contact__item">
          <svg viewBox="0 0 24 24" aria-hidden="true"><path d="M6.6 10.8a15 15 0 0 0 6.6 6.6l2.2-2.2c.3-.3.7-.4 1-.2 1.1.4 2.3.6 3.6.6.6 0 1 .4 1 1V20c0 .6-.4 1-1 1A17 17 0 0 1 3 4c0-.6.4-1 1-1h3.5c.6 0 1 .4 1 1 0 1.3.2 2.5.6 3.6.1.3 0 .7-.2 1z"/></svg>
          <span>888.555.0142</span>
        </li>
        <li class="contact__item">
          <svg viewBox="0 0 24 24" aria-hidden="true"><path d="M2 5h20v2l-10 6L2 7z"/><path d="M2 9l10 6 10-6v10H2z"/></svg>
          <span>info@cedarridgemechanical.com</span>
        </li>
        <li class="contact__item">
          <svg viewBox="0 0 24 24" aria-hidden="true"><circle cx="12" cy="12" r="10" fill="none" stroke="#1e1e1e" stroke-width="2"/><path d="M2 12h20M12 2c3 3 3 17 0 20M12 2c-3 3-3 17 0 20" fill="none" stroke="#1e1e1e" stroke-width="1.6"/></svg>
          <span>www.cedarridgemechanical.com</span>
        </li>
      </ul>
    </div>
  </section>

  <section class="card card--back">
    <div class="brand">
      <span class="brand__mark"></span>
      <span class="brand__name">Cedar Ridge Mechanical</span>
    </div>
  </section>
</main>
</body>
</html>
```